Flat bootstrap design for existing site

I'm looking for a modern flat design based around an existing logo. This has to be a custom design (no external templates), and implemented into a bootstrap framework.

The logo is attached as 2 versions - choose whichever you want, that flows better with whatever design you choose.

Added screenshots of the existing site (currently using the default bootstrap layouts). Please make your designs around those pages in the screenshots (i.e. the homepage only has the postal code input and the header). The active page has 3 screenshots, because I wanted to illustrate the other states that would be visible (in the table rows).

This is a moving/junk removal website, just for some context.

Here's some example websites (flat designs) that I like, just to give you an idea of what I'm after.

https://www.plimvora.com/
https://dacklow.com/
https://trevanu.com/
https://quobrintal.com/en/

Coding

Coded - Design and coding required

Number of Pages Required

5+ page

Colors

Designer to choose colors to be used in the design.

Requirements
Must have
• It must be a modern/simple flat design, that is built around the existing logo (attached).
• It has to be implemented using bootstrap.

```html
<!DOCTYPE html>
<html lang="en">
<head>
<meta charset="utf-8">
<title>Haulvek – Junk Removal</title>
<link href="https://fonts.googleapis.com/css2?family=Open+Sans:wght@400;600;700&display=swap" rel="stylesheet">
<style>
  :root {
    --brand: #4ac9f5;
    --brand-active: #41b5dc;
    --white: #ffffff;
    --ink: #2a2a2a;
    --panel-bg: #f3f3f3;
    --panel-border: #d9d9d9;
    --field-border: #d4d4d4;
  }
  * { box-sizing: border-box; margin: 0; padding: 0; }
  html, body {
    width: 1200px;
    height: 501px;
    overflow: hidden;
    background: var(--white);
    font-family: "Open Sans", Arial, sans-serif;
  }
  .site-header {
    position: relative;
    height: 81px;
    background: var(--brand);
  }
  .brand {
    position: absolute;
    left: 99px;
    top: 0;
    height: 81px;
    display: flex;
    align-items: center;
    gap: 8px;
    color: var(--white);
    font-weight: 700;
    font-size: 30px;
    letter-spacing: 1px;
    text-decoration: none;
  }
  .brand-dot {
    width: 14px;
    height: 14px;
    border-radius: 50%;
    background: var(--white);
  }
  .main-nav {
    position: absolute;
    left: 563px;
    top: 0;
    height: 81px;
    display: flex;
  }
  .main-nav a {
    display: flex;
    align-items: center;
    height: 81px;
    padding: 0 27px;
    color: var(--white);
    font-weight: 700;
    font-size: 14.5px;
    text-decoration: none;
  }
  .main-nav a.is-active { background: var(--brand-active); }
  .booking-panel {
    position: absolute;
    left: 99px;
    top: 187px;
    width: 1002px;
    height: 218px;
    background: var(--panel-bg);
    border: 2px solid var(--panel-border);
    border-radius: 4px;
  }
  .booking-title {
    position: absolute;
    left: 0;
    right: 0;
    top: 46px;
    text-align: center;
    font-size: 26px;
    font-weight: 700;
    color: var(--ink);
  }
  .postal-field {
    position: absolute;
    left: 239px;
    top: 126px;
    width: 391px;
    height: 38px;
    padding: 0 11px;
    border: 2px solid var(--field-border);
    border-radius: 4px;
    background: var(--white);
    font-family: inherit;
    font-size: 14px;
    color: #111;
  }
  .postal-field::placeholder { color: #111; }
  .book-button {
    position: absolute;
    left: 650px;
    top: 126px;
    width: 109px;
    height: 39px;
    border: none;
    border-radius: 4px;
    background: var(--brand);
    color: var(--white);
    font-family: inherit;
    font-size: 16px;
    font-weight: 600;
  }
</style>
</head>
<body>
  <header class="site-header">
    <a class="brand" href="#"><span class="brand-dot"></span>HAULVEK</a>
    <nav class="main-nav">
      <a href="#">BOOK</a>
      <a href="#">HOW IT WORKS</a>
      <a href="#" class="is-active">BECOME A DRIVER</a>
      <a href="#">SIGNIN</a>
    </nav>
  </header>
  <main>
    <section class="booking-panel">
      <h1 class="booking-title">Need junk removed? Book now.</h1>
      <input class="postal-field" type="text" placeholder="Postal code">
      <button class="book-button" type="button">BOOK</button>
    </section>
  </main>
</body>
</html>
```